Business Card for Orthopaedic Clinic.
Should have nice design, double sided that includes logo
Should include my name, my contact, my email, webpage. A QR code to scan business card.

please use dummy information for privacy reasons. I will provide my name, email, practice address once a winner is selected.

Target Market(s)

Future patients

Contact Information for Business Card

Name: Dr Oyel
Contact No: +65 69027314
Practice Address: Singapore
Email: doctor@pelvaro.com
Website: www.pelvaro.com

Colors
00a990

Requirements
Must have
• Logo and a nice colour scheme.
A QR Code for Contact Card.
Name
Contact
Practice Address
Email
Website.
Nice to have
• Nice colour scheme
Should not have
• Nothing too cluttered.

```html
<!DOCTYPE html>
<html lang="en">
<head>
<meta charset="utf-8">
<title>Pelvaro Orthopaedics – Business Card</title>
<link rel="stylesheet" href="https://fonts.googleapis.com/css2?family=Montserrat:wght@400;500;600&display=swap">
<style>
  :root {
    --bg: #2a2a2c;
    --card: #f1f0f0;
    --teal: #00a990;
    --teal-soft: #84bdb7;
    --slate: #5a616a;
    --ink: #1d1d1f;
  }
  * { box-sizing: border-box; margin: 0; padding: 0; }
  html, body {
    width: 1200px; height: 800px; overflow: hidden;
    background: var(--bg);
    font-family: "Montserrat", sans-serif;
  }
  .stage {
    width: 1200px; height: 800px;
    display: flex; flex-direction: column;
    align-items: center; justify-content: center; gap: 28px;
  }
  .card {
    position: relative;
    width: 480px; height: 316px;
    background: var(--card);
  }
  /* Front */
  .card-front {
    display: flex; align-items: center; justify-content: center; gap: 18px;
  }
  .brand-square {
    width: 62px; height: 62px; border-radius: 6px;
    background: var(--teal-soft);
  }
  .brand-name {
    color: var(--slate); font-weight: 500;
    text-transform: uppercase; line-height: 1.15;
  }
  .brand-name .line-main { display: block; font-size: 34px; letter-spacing: 1px; }
  .brand-name .line-sub { display: block; font-size: 19px; letter-spacing: 6px; }
  /* Back */
  .holder-name {
    position: absolute; left: 30px; top: 44px;
    width: 126px; padding-bottom: 8px;
    border-bottom: 1px solid var(--ink);
    color: var(--teal); font-weight: 600;
    font-size: 15px; letter-spacing: 2.5px; text-transform: uppercase;
  }
  .back-mark {
    position: absolute; right: 62px; top: 82px;
    width: 76px; height: 76px; border-radius: 6px;
    background: var(--teal-soft);
  }
  .website {
    position: absolute; right: 14px; top: 170px;
    transform-origin: right top; transform: rotate(-90deg) translateX(0);
    font-size: 10px; letter-spacing: 1.5px; color: var(--ink);
    white-space: nowrap;
  }
  .contact-list {
    position: absolute; left: 30px; bottom: 36px;
    list-style: none; font-size: 11px; letter-spacing: 1.6px;
    line-height: 1.55; color: var(--ink);
  }
</style>
</head>
<body>
<main class="stage">
  <section class="card card-front" aria-label="Card front">
    <span class="brand-square" aria-hidden="true"></span>
    <p class="brand-name">
      <span class="line-main">Pelvaro</span>
      <span class="line-sub">Orthopaedics</span>
    </p>
  </section>

  <section class="card card-back" aria-label="Card back">
    <h1 class="holder-name">Dr Oyel</h1>
    <span class="back-mark" aria-hidden="true"></span>
    <p class="website">www.pelvaro.com</p>
    <ul class="contact-list">
      <li>+65 69027314</li>
      <li>Practice Address: Singapore</li>
      <li>doctor@pelvaro.com</li>
    </ul>
  </section>
</main>
</body>
</html>
```